Branding Pack for new business to business cost saving site

I would like a branding pack for my new project. I would like the following designed;
a4 Presentation folder
Letterhead
Envelope
Business Card
compliment splip

We are a business cost saving site, we have access to 1000s of discount offers for daily business to business offers. I already have the logo therfore please follow th e logo for the coloutr and design.

Target Market(s)

SMEs in United Kingdom

Industry/Entity Type

Business Service

Font styles to use
Serif
Script

Colors
0255a3
fbee3d

Requirements
Must have
• The folder needs to be the same size as attached

```html
<!DOCTYPE html>
<html lang="en">
<head>
<meta charset="utf-8">
<title>thriftmate stationery</title>
<link rel="stylesheet" href="https://fonts.googleapis.com/css2?family=Montserrat:wght@400&family=Pinyon+Script&display=swap">
<style>
  :root {
    --navy: #2d3577;
    --navy-deep: #262d68;
    --yellow: #f7c93b;
    --paper: #ffffff;
    --ink: #2a2f63;
    --backdrop: #d9d9db;
  }
  * { box-sizing: border-box; margin: 0; padding: 0; }
  html, body { width: 1200px; height: 954px; overflow: hidden; }
  body {
    background: var(--backdrop);
    font-family: "Montserrat", Arial, sans-serif;
    font-weight: 400;
    position: relative;
  }
  .folder {
    position: absolute; left: 70px; top: 34px;
    display: flex; box-shadow: 0 10px 30px rgba(0,0,0,.18);
  }
  .folder-panel {
    width: 360px; height: 509px; background: var(--navy);
    position: relative; color: #fff;
  }
  .folder-panel--back { border-right: 1px solid var(--navy-deep); }
  .brand-name { font-size: 32px; line-height: 1; letter-spacing: .5px; white-space: nowrap; }
  .folder-panel .brand-name { color: #fff; }
  .back-name { position: absolute; right: 40px; bottom: 118px; }
  .front-name { position: absolute; left: 50%; top: 72px; transform: translateX(-50%); }
  .front-web { position: absolute; right: 44px; bottom: 36px; font-size: 8px; }
  .contact { display: flex; flex-direction: column; gap: 6px; font-size: 7px; line-height: 1.35; }
  .contact-block { border-left: 2px solid currentColor; padding-left: 6px; }
  .contact-block--lines { border-left-width: 1px; }
  .contact-line { display: flex; align-items: center; gap: 4px; }
  .contact-line svg { width: 7px; height: 7px; flex: none; }
  .folder-contact { position: absolute; left: 44px; bottom: 40px; color: #fff; }
  .slip {
    position: absolute; left: 600px; top: 658px; width: 540px; height: 252px;
    background: var(--paper); box-shadow: 0 6px 18px rgba(0,0,0,.2); overflow: hidden;
  }
  .slip-name { position: absolute; left: 45px; top: 44px; color: var(--ink); }
  .slip-contact { position: absolute; right: 40px; top: 36px; color: var(--ink); }
  .slip-greeting {
    position: absolute; right: 40px; bottom: 36px;
    font-family: "Pinyon Script", cursive; font-size: 24px; color: var(--navy);
  }
  .slip-band { position: absolute; left: 0; bottom: 0; width: 540px; height: 8px; }
</style>
</head>
<body>
  <div class="folder">
    <section class="folder-panel folder-panel--back">
      <span class="brand-name back-name">thriftmate</span>
      <div class="contact folder-contact">
        <div class="contact-block">Level 2, 14 Harbour Rd.<br>Kingsport QLD 4870</div>
        <div class="contact-block contact-block--lines">
          <div class="contact-line"><svg viewBox="0 0 10 10"><path d="M2 1l2 2-1 1.5a6 6 0 0 0 2.5 2.5L7 6l2 2-1.5 1.5C4 9 1 6 .5 2.5z" fill="currentColor"/></svg>+968 24510000</div>
          <div class="contact-line"><svg viewBox="0 0 10 10"><rect x=".5" y="2" width="9" height="6" fill="none" stroke="currentColor"/><path d="M.5 2l4.5 3.5L9.5 2" fill="none" stroke="currentColor"/></svg>info@thriftmate.com</div>
          <div class="contact-line"><svg viewBox="0 0 10 10"><circle cx="5" cy="5" r="4.3" fill="none" stroke="currentColor"/><path d="M.7 5h8.6M5 .7c-2.5 2.5-2.5 6 0 8.6M5 .7c2.5 2.5 2.5 6 0 8.6" fill="none" stroke="currentColor" stroke-width=".7"/></svg>www.thriftmate.com</div>
        </div>
      </div>
    </section>
    <section class="folder-panel folder-panel--front">
      <span class="brand-name front-name">thriftmate</span>
      <span class="front-web">www.thriftmate.com</span>
    </section>
  </div>

  <section class="slip">
    <span class="brand-name slip-name">thriftmate</span>
    <div class="contact slip-contact">
      <div class="contact-block">Level 2, 14 Harbour Rd.<br>Kingsport QLD 4870</div>
      <div class="contact-block contact-block--lines">
        <div class="contact-line"><svg viewBox="0 0 10 10"><path d="M2 1l2 2-1 1.5a6 6 0 0 0 2.5 2.5L7 6l2 2-1.5 1.5C4 9 1 6 .5 2.5z" fill="currentColor"/></svg>+968 24510000</div>
        <div class="contact-line"><svg viewBox="0 0 10 10"><rect x=".5" y="2" width="9" height="6" fill="none" stroke="currentColor"/><path d="M.5 2l4.5 3.5L9.5 2" fill="none" stroke="currentColor"/></svg>info@thriftmate.com</div>
        <div class="contact-line"><svg viewBox="0 0 10 10"><circle cx="5" cy="5" r="4.3" fill="none" stroke="currentColor"/><path d="M.7 5h8.6M5 .7c-2.5 2.5-2.5 6 0 8.6M5 .7c2.5 2.5 2.5 6 0 8.6" fill="none" stroke="currentColor" stroke-width=".7"/></svg>www.thriftmate.com</div>
      </div>
    </div>
    <span class="slip-greeting">With Compliments</span>
    <svg class="slip-band" viewBox="0 0 540 8" preserveAspectRatio="none">
      <polygon points="0,0 332,0 324,8 0,8" fill="var(--navy)"/>
      <polygon points="338,0 540,0 540,8 330,8" fill="var(--yellow)"/>
    </svg>
  </section>
</body>
</html>
```